Velk Partners Building Business Cards

We need a business card that reflects our business as "Solar Experts" in San Diego. Browse our website www.velkpartners.example our License needs to be displayed as "CSLB# 3867140" our phone number is (619) 555-0187

Save thousands on your electric bills and increase the value of your home while helping to protect the environment. Our solar installation experts will help you design the system that's right for you, using only the highest quality equipment that will look great and give you ideal performance. Our goal is to make you energy independent, and get your electric bill to 0.

Paul Osterby
(619) 555-0187
paul@velkpartners.example

Target Market(s)

Home owners in san diego looking for solar

Industry/Entity Type

Solar Energy

Contact Information for Business Card

Paul Osterby
(619) 555-0187
paul@velkpartners.example

Font styles to use
Other font styles liked:
• Use our logo font

Requirements
Must have
• License needs to be displayed as "CSLB# 3867140" our phone number is (619) 555-0187
Nice to have
• Real images of rooftop home solar in san diego
Should not have
• our business address

```html
<!DOCTYPE html>
<html lang="en">
<head>
<meta charset="utf-8">
<title>Velk Partners Building – Business Cards</title>
<link rel="stylesheet" href="https://fonts.googleapis.com/css2?family=Lora:wght@400;700&display=swap">
<style>
  :root {
    --navy: #1f3b73;
    --navy-deep: #1b3570;
    --navy-soft: #2d4a86;
    --sun: #f5a81c;
    --paper: #ffffff;
    --backdrop: #222222;
  }
  * { margin: 0; padding: 0; box-sizing: border-box; }
  html, body {
    width: 1189px;
    height: 1200px;
    overflow: hidden;
    background: var(--backdrop);
    font-family: "Lora", Georgia, serif;
  }
  .card {
    position: absolute;
    left: 166px;
    width: 856px;
    height: 487px;
    border-radius: 22px;
    overflow: hidden;
  }
  .card--front { top: 68px; }
  .card--back { top: 626px; background: var(--paper); }

  .panel-photo {
    position: absolute;
    inset: 0;
    background: linear-gradient(135deg, #2a4681 0%, var(--navy-soft) 45%, #2a4680 70%, #3a5690 100%);
  }

  .brand {
    position: absolute;
    left: 0; right: 0;
    display: flex;
    align-items: center;
    justify-content: center;
    gap: 16px;
  }
  .brand__mark {
    width: 40px; height: 40px;
    border-radius: 50%;
    background: var(--sun);
    flex: none;
  }
  .brand__name {
    font-weight: 700;
    font-size: 52px;
    letter-spacing: -0.5px;
    line-height: 1;
    white-space: nowrap;
  }
  .card--front .brand { top: 146px; }
  .card--front .brand__name { color: var(--paper); }
  .card--back .brand { top: 74px; }
  .card--back .brand__name { color: var(--navy); }

  .social {
    position: absolute;
    top: 335px;
    left: 0; right: 0;
    display: flex;
    justify-content: center;
    gap: 18px;
  }
  .social__item {
    width: 35px; height: 35px;
    border-radius: 3px;
    background: var(--paper);
  }

  .contact {
    position: absolute;
    top: 228px;
    left: 0; right: 0;
    text-align: center;
    color: var(--navy);
  }
  .contact__name {
    font-weight: 700;
    font-size: 30px;
    letter-spacing: 0.5px;
    text-transform: uppercase;
    margin-bottom: 34px;
  }
  .contact__line {
    font-size: 23px;
    line-height: 31px;
  }
  .contact__label { color: var(--sun); }

  .footer-band {
    position: absolute;
    left: 0; bottom: 0;
    width: 856px; height: 70px;
  }
  .website {
    position: absolute;
    left: 0; right: 0;
    bottom: 12px;
    text-align: center;
    font-size: 23px;
    color: var(--paper);
  }
  .website__domain { color: var(--sun); }
</style>
</head>
<body>
  <section class="card card--front">
    <div class="panel-photo" role="img" aria-label="Close-up of rooftop solar panels under a deep blue tint"></div>
    <div class="brand">
      <span class="brand__mark"></span>
      <span class="brand__name">Velk Partners Building</span>
    </div>
    <div class="social" aria-label="Social media links">
      <span class="social__item"></span>
      <span class="social__item"></span>
      <span class="social__item"></span>
      <span class="social__item"></span>
    </div>
  </section>

  <section class="card card--back">
    <div class="brand">
      <span class="brand__mark"></span>
      <span class="brand__name">Velk Partners Building</span>
    </div>
    <div class="contact">
      <p class="contact__name">Paul Osterby</p>
      <p class="contact__line"><span class="contact__label">Phone:</span> (619) 555-0187</p>
      <p class="contact__line"><span class="contact__label">Email:</span> paul@velkpartners.example</p>
      <p class="contact__line">CSLB# 3867140</p>
    </div>
    <svg class="footer-band" viewBox="0 0 856 70" preserveAspectRatio="none" aria-hidden="true">
      <path d="M0 42 Q428 -18 856 42 L856 70 L0 70 Z" fill="var(--sun)"/>
      <path d="M0 50 Q428 -8 856 50 L856 70 L0 70 Z" fill="var(--navy-deep)"/>
    </svg>
    <p class="website">www.<span class="website__domain">velkpartners</span>.example</p>
  </section>
</body>
</html>
```